Healthcare and Professional IT Services Company need a redesigned business card

We are a IT Services company that targets small medical practices and professional business such as Attorneys, Accounts, Architects etc. We want to communicate a professional yet friendly image using recent logo redesign here on ArtHarbor. Like to see the colors blue and orange in the design. Must use the Tall Pine Computing as displayed in the new logo - then also want to incorporate the fish logo as well.

Target Market(s)

Small medical and professional services

Industry/Entity Type

It Company

Contact Information for Business Card

The usual stuff, place for name address phone website. Also maybe our tagline which is "Rooted in technology"

Requirements
Must have
• My new logo and the fish somewhere on the card

```html
<!DOCTYPE html>
<html lang="en">
<head>
<meta charset="utf-8">
<title>Tall Pine Computing – Business Card</title>
<link rel="stylesheet" href="https://fonts.googleapis.com/css2?family=Open+Sans:wght@400;600;700&display=swap">
<style>
  :root {
    --brand-blue: #129fdf;
    --brand-blue-deep: #0b8fd0;
    --brand-blue-faint: #2aaae4;
    --accent-orange: #f7941d;
    --ink: #3d3d3d;
    --paper: #fbfbfb;
    --backdrop: #d9d9d9;
  }
  * { box-sizing: border-box; margin: 0; padding: 0; }
  html, body { width: 1200px; height: 900px; overflow: hidden; }
  body {
    background: var(--backdrop);
    font-family: "Open Sans", Arial, sans-serif;
    display: flex;
    flex-direction: column;
    align-items: center;
    justify-content: center;
    gap: 24px;
  }
  .card {
    position: relative;
    width: 700px;
    height: 400px;
    overflow: hidden;
    box-shadow: 0 6px 18px rgba(0,0,0,0.18);
  }

  /* Front */
  .card--front { background: var(--brand-blue); }
  .front__mark-decor {
    position: absolute;
    left: 230px; top: 40px;
    width: 340px; height: 320px;
    border-radius: 48% 52% 45% 55%;
    background: var(--brand-blue-faint);
    opacity: 0.55;
  }
  .front__wordmark {
    position: absolute;
    left: 0; right: 0; top: 168px;
    text-align: center;
    color: #ffffff;
    font-weight: 700;
    font-size: 46px;
    letter-spacing: -0.5px;
  }

  /* Back */
  .card--back { background: var(--paper); }
  .back__band {
    position: absolute;
    left: 0; right: 0; top: 292px;
    height: 58px;
    background: var(--brand-blue);
  }
  .back__tagline {
    position: absolute;
    left: 48px; top: 308px;
    color: #ffffff;
    font-size: 18px;
    letter-spacing: 1px;
  }
  .back__fish-illustration {
    position: absolute;
    left: 110px; top: 36px;
    width: 150px; height: 118px;
    border-radius: 40% 50% 45% 40%;
    background: #d3ecf8;
  }
  .back__fish-illustration--small {
    left: 560px; top: 270px;
    width: 96px; height: 84px;
    background: #e3f3fb;
  }
  .back__wordmark {
    position: absolute;
    left: 44px; top: 168px;
    width: 300px;
    color: var(--brand-blue-deep);
    font-weight: 700;
    font-size: 30px;
    line-height: 1.1;
  }
  .contact {
    position: absolute;
    left: 390px; top: 96px;
    color: var(--ink);
    font-size: 14px;
    line-height: 1.5;
  }
  .contact__name {
    color: var(--brand-blue-deep);
    font-weight: 700;
    font-size: 24px;
    line-height: 1.1;
  }
  .contact__title {
    color: var(--accent-orange);
    font-size: 15px;
    margin-bottom: 10px;
  }
  .contact__row { display: flex; align-items: center; gap: 8px; }
  .contact__row svg { width: 13px; height: 13px; flex: none; }
  .contact__address { padding-left: 21px; }
</style>
</head>
<body>

<section class="card card--front" aria-label="Card front">
  <div class="front__mark-decor" role="img" aria-label="Faint brand mascot watermark"></div>
  <div class="front__wordmark">Tall Pine Computing</div>
</section>

<section class="card card--back" aria-label="Card back">
  <div class="back__band"></div>
  <div class="back__tagline">Rooted in technology</div>

  <div class="back__fish-illustration" role="img" aria-label="Blue line illustration of the brand mascot"></div>
  <div class="back__wordmark">Tall Pine Computing</div>

  <div class="contact">
    <div class="contact__name">Ellis Warren</div>
    <div class="contact__title">CEO/Founder</div>
    <div class="contact__address">4210 Cedar Ridge Road<br>Fairbanks, Alaska 99701</div>
    <div class="contact__row">
      <svg viewBox="0 0 16 16" aria-hidden="true"><path fill="#129fdf" d="M3.6 1.5l2.3 2.6-1.2 1.7c.9 2 2.6 3.7 4.6 4.6l1.7-1.2 2.6 2.3-1.3 2.5C7 13.6 2.4 9 1.1 3z"/></svg>
      <span>907 555 0148</span>
    </div>
    <div class="contact__row">
      <svg viewBox="0 0 16 16" aria-hidden="true"><rect x="1" y="3" width="14" height="10" fill="#129fdf"/><path d="M1.5 3.5L8 9l6.5-5.5" stroke="#fff" stroke-width="1.3" fill="none"/></svg>
      <span>hello@tallpine.example</span>
    </div>
    <div class="contact__row">
      <svg viewBox="0 0 16 16" aria-hidden="true"><circle cx="8" cy="8" r="7" fill="#129fdf"/><path d="M1 8h14M8 1c-3 3-3 11 0 14M8 1c3 3 3 11 0 14" stroke="#fff" stroke-width="1" fill="none"/></svg>
      <span>www.tallpine.example</span>
    </div>
  </div>

  <div class="back__fish-illustration back__fish-illustration--small" role="img" aria-label="Small mascot illustration peeking over the band"></div>
</section>

</body>
</html>
```